We need a complete design for our construction company KELTO CONSTRUCTION based in Auckland New Zealand, we need a logo, website, business card, vehicle design etc..
We are a mid to high-end construction company who work mostly on residential projects and some commercial.

What we want to see in the design;
Professional,
Architectural,
Simple,
Alternative,

We want the design to communicate professionalism, high quality wormanship and and quality service.

Target Market(s)

People looking for a quality building/ construction company

Industry/Entity Type

Construction Company

Contact Information for Business Card

KELTO CONSTRUCTION.co.nz
Lino Verasek
lino@keltoconstruction.example.nz
021 5807 462

Logo Text

KELTO CONSTRUCTION

Number of Pages Required

5+ page

Font styles to use
Sans Serif

Colors

Designer to choose colors to be used in the design.

Requirements
Must have
• Must appear high end, professional, quality, be simple, easy to use, give security to potential clients
Nice to have
• high-quality photos of our recent projects
• about us page
• blog page
• contact us page
• high quality content
Should not have
• should not be hard to use and have too much going on.

```html
<!DOCTYPE html>
<html lang="en">
<head>
<meta charset="utf-8">
<title>KELTO CONSTRUCTION</title>
<link rel="stylesheet" href="https://fonts.googleapis.com/css2?family=Raleway:wght@500;600;700;800&family=Open+Sans:wght@400;600;700&display=swap">
<style>
:root{
  --red:#b5121b;
  --red-dark:#8e0d14;
  --ink:#222;
  --text:#555;
  --dark:#2b2b2b;
  --black:#111;
  --white:#fff;
  --line:#e4e4e4;
}
*{box-sizing:border-box;margin:0;padding:0}
html,body{width:1200px;height:3974px;overflow:hidden}
body{position:relative;background:var(--white);font-family:"Open Sans",Arial,sans-serif;color:var(--text)}
.abs{position:absolute}
h1,h2,h3,h4{font-family:"Raleway",Arial,sans-serif}
.btn{position:absolute;display:flex;align-items:center;justify-content:center;background:var(--dark);color:var(--white);font:600 19px "Open Sans",Arial,sans-serif;letter-spacing:.5px;text-transform:uppercase}
.section-title{position:absolute;left:0;width:1200px;text-align:center;font-weight:600;font-size:37px;color:var(--ink)}
.section-title .accent{color:var(--red)}
.lead{position:absolute;left:170px;width:860px;text-align:center;font-size:13.5px;line-height:24px;color:var(--text)}
.on-red{color:var(--white)}

/* header */
.hero{position:absolute;left:0;top:0;width:1200px;height:678px;background:linear-gradient(100deg,#eef1f4 0%,#dde3e8 40%,#a9b6c0 70%,#7d8d99 100%)}
.hero-figures{position:absolute;left:500px;top:150px;width:560px;height:528px;background:linear-gradient(160deg,#e6842a 0%,#c96a1e 30%,#4f5f6e 70%,#3a4652 100%);border-radius:160px 160px 0 0;opacity:.85}
.topbar{position:absolute;left:660px;top:0;width:540px;height:48px;background:var(--dark);display:flex;align-items:center;justify-content:flex-end;gap:40px;padding-right:80px;color:var(--white);font-size:15px}
.topbar span{display:flex;align-items:center;gap:8px}
.social{position:absolute;left:184px;top:10px;display:flex;gap:6px}
.social i{display:block;width:24px;height:24px;background:var(--red);border:2px solid var(--white)}
.brand{position:absolute;left:82px;top:52px;display:flex;align-items:center;gap:12px;color:var(--red);font:700 22px/1 "Raleway",Arial,sans-serif}
.brand .mark{width:36px;height:36px;background:var(--red)}
.brand .name{display:flex;flex-direction:column;gap:6px}
.brand .name b{font-size:42px;font-weight:700;letter-spacing:1px}
.brand .name small{font-size:16px;font-weight:700;letter-spacing:4px}
.nav{position:absolute;top:86px;left:560px;display:flex;gap:48px;font-size:17px;color:#333}
.nav .active{color:var(--red);font-weight:600}
.hero-title{position:absolute;left:80px;top:250px;font:800 49px/54px "Raleway",Arial,sans-serif;color:var(--red)}
.hero-text{position:absolute;left:80px;top:374px;width:360px;font-size:17px;line-height:27px;color:#333}

/* about */
.band{position:absolute;left:0;width:1200px;background:var(--red)}
.feature{position:absolute;top:1332px;width:324px;height:294px;background:var(--white);padding:10px;box-shadow:0 2px 8px rgba(0,0,0,.12)}
.feature .photo{height:200px}
.feature .caption{position:absolute;left:10px;right:10px;bottom:10px;height:74px;background:var(--red);color:var(--white);font-size:21px;line-height:25px;display:flex;align-items:center;padding:0 80px 0 14px}
.feature .caption .icon{position:absolute;right:8px;top:8px;width:58px;height:58px;background:var(--white);display:flex;align-items:center;justify-content:center}

/* projects */
.filters{position:absolute;top:1834px;left:0;width:1200px;display:flex;justify-content:center;gap:44px;font-size:19px;color:#333}
.filters span{padding:8px 0}
.filters .on{background:var(--red);color:var(--white);border-radius:24px;padding:8px 20px}
.grid{position:absolute;top:1928px;left:0;width:1200px;height:522px;display:grid;grid-template-columns:repeat(4,300px);grid-template-rows:repeat(2,261px)}
.arrow{position:absolute;top:2163px;width:50px;height:50px;border-radius:50%;display:flex;align-items:center;justify-content:center}

/* blog */
.post{position:absolute;top:2877px;width:324px;background:var(--white)}
.post .photo{height:223px;border:10px solid var(--white);border-bottom:0;box-shadow:0 2px 8px rgba(0,0,0,.12)}
.post h3{margin-top:28px;font:500 23px/29px "Raleway",Arial,sans-serif;color:var(--red)}
.post .meta{margin-top:16px;display:flex;gap:30px;font-size:15px;color:#444}
.post .meta span{display:flex;align-items:center;gap:8px}
.post p{margin-top:14px;font-size:14px;line-height:23px;color:var(--text)}
.post .more{display:inline-block;margin-top:16px;font-size:15px;font-weight:700;color:var(--red);text-decoration:underline}

/* footer */
.footer{position:absolute;left:0;top:3438px;width:1200px;height:472px;background:var(--red);color:var(--white)}
.footer h4{position:absolute;top:74px;font-size:22px;font-weight:700}
.field{position:absolute;background:var(--white);color:#888;font-size:13px;padding:10px 12px}
.footer .small{font-size:13.5px;line-height:24px}
.contact-line{position:absolute;display:flex;gap:16px;font-size:13.5px;line-height:24px}
.links{position:absolute;left:720px;top:138px;list-style:none;font-size:14px}
.links li{height:37px;display:flex;align-items:center;gap:14px}
.links li::before{content:"";width:7px;height:7px;background:var(--white)}
.skyline{position:absolute;left:344px;top:350px;width:560px;height:122px;background:linear-gradient(180deg,rgba(0,0,0,0) 0%,rgba(0,0,0,.28) 100%)}
.copyright{position:absolute;left:0;top:3910px;width:1200px;height:64px;background:var(--black);color:#ddd;font-size:14px;display:flex;align-items:center;justify-content:center}
.copyright b{margin:0 4px;color:var(--white)}
</style>
</head>
<body>

<!-- header / hero -->
<div class="hero" role="img" aria-label="Two site engineers in hard hats reviewing plans on a tablet by a bridge"></div>
<div class="hero-figures" role="img" aria-label="Engineers in high-visibility vests and hard hats"></div>
<div class="topbar">
  <span><svg width="16" height="16" viewBox="0 0 24 24" fill="#fff"><path d="M6.6 10.8a15 15 0 0 0 6.6 6.6l2.2-2.2a1 1 0 0 1 1-.25 11.4 11.4 0 0 0 3.6.6 1 1 0 0 1 1 1V20a1 1 0 0 1-1 1A17 17 0 0 1 3 4a1 1 0 0 1 1-1h3.5a1 1 0 0 1 1 1c0 1.25.2 2.45.6 3.6a1 1 0 0 1-.25 1z"/></svg>+64 9 555 0142</span>
  <span><svg width="14" height="18" viewBox="0 0 24 30" fill="#fff"><path d="M12 0a10 10 0 0 0-10 10c0 7.5 10 20 10 20s10-12.5 10-20A10 10 0 0 0 12 0zm0 14a4 4 0 1 1 0-8 4 4 0 0 1 0 8z"/></svg>48 Harbour Lane, Ponsonby.</span>
</div>
<div class="social"><i></i><i></i><i></i><i></i></div>
<div class="brand"><span class="mark"></span><span class="name"><b>KELTO</b><small>CONSTRUCTION</small></span></div>
<nav class="nav">
  <span class="active">Home</span><span>About</span><span>Projects &#8964;</span><span>Blog</span><span>Contact</span>
  <svg width="22" height="22" viewBox="0 0 24 24" fill="none" stroke="#b5121b" stroke-width="2.5"><circle cx="10" cy="10" r="7"/><path d="M15 15l6 6"/></svg>
</nav>
<h1 class="hero-title">WE BUILD YOUR<br>DREAM</h1>
<p class="hero-text">Lorem Ipsum is simply dummy text of the printing and typesetting industry.</p>
<div class="btn" style="left:80px;top:450px;width:153px;height:64px">Contact Us</div>

<!-- welcome -->
<h2 class="section-title" style="top:738px">Welcome to <span class="accent">KELTO</span> Construction</h2>
<p class="lead" style="top:795px">Lorem Ipsum is simply dummy text of the printing and typesetting industry. Lorem Ipsum has been the industry's standard dummy text ever since the 1500s, when an unknown printer took a galley of type and scrambled it to make a type specimen book. It has survived not only five centuries, but also the leap into electronic typesetting, remaining essentially unchanged. It was popularised in the 1960s with the release of Letraset sheets containing Lorem Ipsum passages, and more recently with desktop publishing software like Aldus PageMaker including versions of Lorem Ipsum.</p>
<div class="btn" style="left:522px;top:959px;width:156px;height:63px">Read More</div>

<!-- about -->
<div class="band" style="top:1086px;height:318px"></div>
<h2 class="section-title on-red" style="top:1143px;color:#fff">About KELTO Construction</h2>
<p class="lead on-red" style="top:1208px;color:#fff">Lorem Ipsum is simply dummy text of the printing and typesetting industry. Lorem Ipsum has been the industry's standard dummy text ever since the 1500s, when an unknown printer took a galley of type and scrambled it to make a type specimen book. It has survived not only five centuries, but also the leap into electronic typesetting, remaining essentially unchanged.</p>

<div class="feature" style="left:80px">
  <div class="photo" role="img" aria-label="Two clients discussing plans at a desk" style="background:linear-gradient(135deg,#f4f4f4,#c8d0d8 60%,#9aa6b2)"></div>
  <div class="caption">Communicate professionalism<span class="icon"><svg width="36" height="36" viewBox="0 0 36 36" fill="#b5121b"><circle cx="10" cy="9" r="4"/><circle cx="26" cy="9" r="4"/><rect x="4" y="15" width="12" height="10"/><rect x="20" y="15" width="12" height="10"/><rect x="2" y="27" width="32" height="3"/></svg></span></div>
</div>
<div class="feature" style="left:437px">
  <div class="photo" role="img" aria-label="Builder in a hard hat laying concrete blocks" style="background:linear-gradient(160deg,#6f9fcf,#b7c2cc 55%,#8a7a66)"></div>
  <div class="caption">High quality wormanship<span class="icon"><svg width="36" height="36" viewBox="0 0 36 36" fill="#2b2b2b"><path d="M8 15a10 10 0 0 1 20 0z"/><rect x="6" y="15" width="24" height="3"/><circle cx="18" cy="23" r="5"/><path d="M8 36a10 8 0 0 1 20 0z"/></svg></span></div>
</div>
<div class="feature" style="left:795px">
  <div class="photo" role="img" aria-label="Finished timber-framed living room interior" style="background:linear-gradient(135deg,#8a5a34,#c9a07a 50%,#e8dccb)"></div>
  <div class="caption">quality service<span class="icon"><svg width="36" height="36" viewBox="0 0 36 36" fill="#2b2b2b"><circle cx="18" cy="14" r="11"/><circle cx="18" cy="14" r="6" fill="#fff"/><path d="M11 23l-3 12 5-3 3 4 2-10zM25 23l3 12-5-3-3 4-2-10z"/></svg></span></div>
</div>

<!-- projects -->
<h2 class="section-title" style="top:1695px"><span class="accent">KELTO</span> Projects</h2>
<p class="lead" style="top:1757px;left:260px;width:680px">Lorem Ipsum is simply dummy text of the printing and typesetting industry. Lorem Ipsum has been the industry's standard dummy text ever since the 1500s.</p>
<div class="filters"><span class="on">Show All</span><span>Commercial</span><span>Residential</span><span>Construction</span></div>
<div class="grid">
  <div role="img" aria-label="Modern white house with reflecting pool" style="background:linear-gradient(160deg,#e9eef2,#aab8c4 60%,#5d6f7e)"></div>
  <div role="img" aria-label="Minimal dining room interior" style="background:linear-gradient(160deg,#f0efec,#c9c6bf 60%,#5a4d40)"></div>
  <div role="img" aria-label="Rooftop terrace at dusk" style="background:linear-gradient(160deg,#2c4a7a,#7d8db0 50%,#d8a85a)"></div>
  <div role="img" aria-label="Timber-clad lounge with sofas" style="background:linear-gradient(160deg,#6b4426,#a07050 50%,#d9cfc2)"></div>
  <div role="img" aria-label="Covered patio with glass walls" style="background:linear-gradient(160deg,#d8dde0,#8e9aa2 60%,#3c4a52)"></div>
  <div role="img" aria-label="Apartment towers lit at night by water" style="background:linear-gradient(180deg,#3b6fb0,#274a78 55%,#c28a38)"></div>
  <div role="img" aria-label="White modern kitchen" style="background:linear-gradient(160deg,#fafafa,#d6d6d6 60%,#9a9a9a)"></div>
  <div role="img" aria-label="House with pool lit at twilight" style="background:linear-gradient(180deg,#2e3e66,#a0663a 55%,#2aa0c8)"></div>
</div>
<div class="arrow" style="left:50px;background:#fff"><svg width="16" height="16" viewBox="0 0 16 16"><path d="M10 2L4 8l6 6" fill="none" stroke="#222" stroke-width="2.5"/></svg></div>
<div class="arrow" style="left:1098px;background:var(--red)"><svg width="16" height="16" viewBox="0 0 16 16"><path d="M6 2l6 6-6 6" fill="none" stroke="#fff" stroke-width="2.5"/></svg></div>
<div class="btn" style="left:522px;top:2514px;width:156px;height:61px">View All</div>

<!-- news -->
<div class="band" style="top:2638px;height:302px"></div>
<h2 class="section-title" style="top:2696px;color:#fff">News &amp; Blog</h2>
<p class="lead" style="top:2759px;color:#fff">Lorem Ipsum is simply dummy text of the printing and typesetting industry. Lorem Ipsum has been the industry's standard dummy text ever since the 1500s, when an unknown printer took a galley of type and scrambled it to make a type specimen book. It has survived not only five centuries, but also the leap into electronic typesetting, remaining essentially unchanged.</p>

<article class="post" style="left:80px">
  <div class="photo" role="img" aria-label="Workers on a building site viewed from above" style="background:linear-gradient(160deg,#a08a6a,#c9b89a 50%,#6a5a48)"></div>
  <h3>What a Difference a Few Months Make</h3>
  <div class="meta"><span><svg width="14" height="15" viewBox="0 0 14 15" fill="#333"><circle cx="7" cy="4" r="4"/><path d="M0 15a7 6 0 0 1 14 0z"/></svg>By Admin</span><span><svg width="15" height="15" viewBox="0 0 16 16" fill="none" stroke="#333" stroke-width="2"><circle cx="8" cy="8" r="6.5"/><path d="M8 4v4l3 2"/></svg>19 March 2018</span></div>
  <p>Lorem Ipsum is simply dummy text of the printing and typesetting industry. Lorem Ipsum has been the industry's standard dummy text ever since the 1500s.</p>
  <span class="more">READ MORE</span>
</article>
<article class="post" style="left:437px">
  <div class="photo" role="img" aria-label="Builder holding a yellow hard hat and tool belt" style="background:linear-gradient(160deg,#5a4a3e,#8a6e54 50%,#d8b23a)"></div>
  <h3>What a Difference a Few Months Make</h3>
  <div class="meta"><span><svg width="14" height="15" viewBox="0 0 14 15" fill="#333"><circle cx="7" cy="4" r="4"/><path d="M0 15a7 6 0 0 1 14 0z"/></svg>By Admin</span><span><svg width="15" height="15" viewBox="0 0 16 16" fill="none" stroke="#333" stroke-width="2"><circle cx="8" cy="8" r="6.5"/><path d="M8 4v4l3 2"/></svg>19 March 2018</span></div>
  <p>Lorem Ipsum is simply dummy text of the printing and typesetting industry. Lorem Ipsum has been the industry's standard dummy text ever since the 1500s.</p>
  <span class="more">READ MORE</span>
</article>
<article class="post" style="left:795px">
  <div class="photo" role="img" aria-label="Team in high-visibility vests inspecting a timber frame" style="background:linear-gradient(160deg,#d9c9a8,#c4a070 50%,#d8d440)"></div>
  <h3>What a Difference a Few Months Make</h3>
  <div class="meta"><span><svg width="14" height="15" viewBox="0 0 14 15" fill="#333"><circle cx="7" cy="4" r="4"/><path d="M0 15a7 6 0 0 1 14 0z"/></svg>By Admin</span><span><svg width="15" height="15" viewBox="0 0 16 16" fill="none" stroke="#333" stroke-width="2"><circle cx="8" cy="8" r="6.5"/><path d="M8 4v4l3 2"/></svg>19 March 2018</span></div>
  <p>Lorem Ipsum is simply dummy text of the printing and typesetting industry. Lorem Ipsum has been the industry's standard dummy text ever since the 1500s.</p>
  <span class="more">READ MORE</span>
</article>

<!-- footer -->
<footer class="footer">
  <div class="skyline" role="img" aria-label="Silhouette of a city skyline with construction cranes"></div>

  <h4 style="left:80px">Contact Us</h4>
  <div class="field" style="left:80px;top:143px;width:144px;height:48px">Name :</div>
  <div class="field" style="left:233px;top:143px;width:146px;height:48px">Email :</div>
  <div class="field" style="left:80px;top:199px;width:299px;height:53px">Message :</div>
  <div class="btn" style="left:80px;top:265px;width:164px;height:56px;font-size:15px">Send Message</div>

  <h4 style="left:424px">About Company</h4>
  <p class="small abs" style="left:424px;top:136px;width:260px">Lorem Ipsum is simply dummy text of the printing and typesetting industry.</p>
  <div class="contact-line" style="left:424px;top:198px;width:260px"><svg width="16" height="20" viewBox="0 0 24 30" fill="#fff" style="flex:none;margin-top:4px"><path d="M12 0a10 10 0 0 0-10 10c0 7.5 10 20 10 20s10-12.5 10-20A10 10 0 0 0 12 0zm0 14a4 4 0 1 1 0-8 4 4 0 0 1 0 8z"/></svg><span>48 Harbour Lane, Ponsonby,<br>Auckland, NZ - 1011</span></div>
  <div class="contact-line" style="left:424px;top:260px"><svg width="16" height="16" viewBox="0 0 24 24" fill="#fff" style="margin-top:4px"><path d="M6.6 10.8a15 15 0 0 0 6.6 6.6l2.2-2.2a1 1 0 0 1 1-.25 11.4 11.4 0 0 0 3.6.6 1 1 0 0 1 1 1V20a1 1 0 0 1-1 1A17 17 0 0 1 3 4a1 1 0 0 1 1-1h3.5a1 1 0 0 1 1 1c0 1.25.2 2.45.6 3.6a1 1 0 0 1-.25 1z"/></svg><span>+64 9 555 0142</span></div>
  <div class="contact-line" style="left:424px;top:302px"><svg width="18" height="14" viewBox="0 0 18 14" fill="none" stroke="#fff" stroke-width="1.8" style="margin-top:5px"><rect x="1" y="1" width="16" height="12"/><path d="M1 1l8 7 8-7"/></svg><span>info@kelto.example</span></div>

  <h4 style="left:720px">Navigation</h4>
  <ul class="links"><li>Home</li><li>About</li><li>Projects</li><li>Blog</li><li>Contact</li></ul>

  <h4 style="left:895px">Newsletter</h4>
  <p class="small abs" style="left:895px;top:136px;width:250px">Would you like to receive exclusive access to articles, white papers and our regular monthly newsletter?</p>
  <div class="field" style="left:895px;top:223px;width:228px;height:53px;display:flex;align-items:center">Enter Email Id</div>
  <div class="btn" style="left:895px;top:289px;width:155px;height:56px;font-size:17px">Subscribe</div>
</footer>
<div class="copyright">Copyright &copy; 2018, <b>KELTO CONSTRUCTION</b>. All rights reserved. Privacy Policy.</div>

</body>
</html>
```